BOLD & MINIMALIST DESIGN NEEDED

We want a very bold but minimalistic business card design that is impactful and utilizes both sides of the business card. Our current logo is included for your use.

We want bold fonts and good use of negative space. We don't want the logo to overpower the design.

Target Market(s)

Professionals who are building new commercial buildings.

Industry/Entity Type

Construction

Contact Information for Business Card

Name, Title, email, office phone, cell phone, website

Font styles to use
Serif
Sans Serif

Requirements
Must have
• Bold design!

```html
<!DOCTYPE html>
<html lang="en">
<head>
<meta charset="utf-8">
<title>Ridgeway Design + Build – Business Card</title>
<link rel="stylesheet" href="https://fonts.googleapis.com/css2?family=Montserrat:wght@400;500;700;800&display=swap">
<style>
  :root {
    --backdrop: #969696;
    --brand-green: #86c440;
    --brand-green-light: #92cc55;
    --brand-green-deep: #4f8a3c;
    --card-black: #151515;
    --ink-white: #ffffff;
    --card-radius: 28px;
  }
  * { margin: 0; padding: 0; box-sizing: border-box; }
  html, body {
    width: 1200px;
    height: 1108px;
    overflow: hidden;
    background: var(--backdrop);
    font-family: "Montserrat", sans-serif;
  }
  .canvas { position: relative; width: 1200px; height: 1108px; }

  .card {
    position: absolute;
    left: 240px;
    width: 718px;
    height: 411px;
    border-radius: var(--card-radius);
    overflow: hidden;
  }

  /* Front */
  .card-front {
    top: 119px;
    background: linear-gradient(125deg, var(--brand-green) 0%, var(--brand-green) 45%, var(--brand-green-light) 60%, var(--brand-green) 100%);
    display: flex;
    align-items: center;
    justify-content: center;
  }
  .front-wordmark {
    font-weight: 800;
    font-size: 66px;
    letter-spacing: 2px;
    color: var(--brand-green-deep);
  }

  /* Back */
  .card-back { top: 580px; background: var(--card-black); }

  .company-name {
    position: absolute;
    top: 118px;
    left: 0;
    width: 100%;
    text-align: center;
    color: var(--ink-white);
    font-weight: 700;
    line-height: 1;
  }
  .company-name .name-main { display: block; font-size: 40px; letter-spacing: 1px; }
  .company-name .name-sub { display: block; font-size: 15px; letter-spacing: 7px; margin-top: 8px; }

  .person {
    position: absolute;
    right: 389px;
    top: 244px;
    text-align: right;
  }
  .person-name {
    font-weight: 700;
    font-size: 35px;
    color: var(--brand-green);
    letter-spacing: 0.5px;
    line-height: 1;
  }
  .person-title {
    margin-top: 12px;
    font-weight: 400;
    font-size: 18px;
    color: var(--ink-white);
    line-height: 1;
  }

  .divider {
    position: absolute;
    left: 356px;
    top: 225px;
    width: 2px;
    height: 101px;
    background: var(--brand-green);
  }

  .contact-list {
    position: absolute;
    left: 384px;
    top: 217px;
    list-style: none;
  }
  .contact-list li {
    display: flex;
    align-items: center;
    height: 28.7px;
    font-size: 19px;
    color: var(--ink-white);
    letter-spacing: 0.3px;
  }
  .contact-icon { width: 16px; height: 16px; margin-right: 10px; flex: none; }

  .address-band {
    position: absolute;
    left: 0;
    top: 360px;
    width: 100%;
    height: 25px;
    background: var(--brand-green);
    color: var(--ink-white);
    font-size: 17px;
    text-align: center;
    line-height: 25px;
  }
</style>
</head>
<body>
<main class="canvas">

  <section class="card card-front" aria-label="Card front">
    <span class="front-wordmark">RIDGEWAY</span>
  </section>

  <section class="card card-back" aria-label="Card back">
    <div class="company-name">
      <span class="name-main">RIDGEWAY</span>
      <span class="name-sub">DESIGN + BUILD</span>
    </div>

    <div class="person">
      <p class="person-name">MARCUS HALE</p>
      <p class="person-title">OWNER-CEO</p>
    </div>

    <div class="divider"></div>

    <ul class="contact-list">
      <li>
        <svg class="contact-icon" viewBox="0 0 16 16" aria-hidden="true"><path fill="#86c440" d="M1 6c0-2 3-3 7-3s7 1 7 3v1h-3V5.5H4V7H1zM4 8h8l2 5H2z"/><circle cx="8" cy="10.5" r="1.5" fill="#151515"/></svg>
        123 456 789
      </li>
      <li>
        <svg class="contact-icon" viewBox="0 0 16 16" aria-hidden="true"><rect x="4" y="1" width="8" height="14" rx="1.5" fill="none" stroke="#86c440" stroke-width="1.6"/><circle cx="8" cy="12.5" r="0.9" fill="#86c440"/></svg>
        123 456 789
      </li>
      <li>
        <svg class="contact-icon" viewBox="0 0 16 16" aria-hidden="true"><rect x="1" y="3.5" width="14" height="9" fill="#86c440"/><path d="M1 3.5l7 5 7-5M1 12.5l5-4.5M15 12.5l-5-4.5" fill="none" stroke="#151515" stroke-width="1"/></svg>
        info@yourgmail.com
      </li>
      <li>
        <svg class="contact-icon" viewBox="0 0 16 16" aria-hidden="true"><circle cx="8" cy="8" r="7" fill="#86c440"/><path d="M4 4c2 1 2 3 4 3s1 3 0 4-1 3-2 3M11 3c0 2 2 2 3 3" fill="none" stroke="#151515" stroke-width="1.3"/></svg>
        www.yourwebsite.com
      </li>
    </ul>

    <div class="address-band">Your address, City State, Zip 1234</div>
  </section>

</main>
</body>
</html>
```